Product Description page for Hullwrap.com, References here just need a clean up redesign

Hi, were working on updating the product description page of our site hullwrap.com

Attached is a reference of what we drew on paint. We want to keep it pretty much the same as far as whats on there, the components with a few small adjustments and a clean actually designed look.

1. We want to remove the tabs (product description, warranty, reviews) and put it all in that main content area stretching down into sections. IE: Product Description section, followed by reviews, followed by warranty, below each other.
2. The side bar needs to be redesigned as far as the look and feel but the content and whats in there should stay the same.
3. The main banner area will be replaced shortly you do not have to worry about that.
4. Include a section or box for people to put in their email for a free Ebook.

Target Market(s)

people looking to easily view our boat cover products and buy without having to click too often or leave the page.

Industry/Entity Type

Online Shopping

Number of Pages Required

1 page

Requirements
Must have
• - Must update the sidebar
• - Must update the content area to remove the tabs and put the content from each tab sectioned off below each other (dummy text is fine for now for the tabs you cant view)
Nice to have
• - Cool place thats clean and functional to insert a section for people to put in their email to receive a free ebook
Should not have
• - too much change, we already know what we want and have a solid reference to work from.

```html
<!DOCTYPE html>
<html lang="en">
<head>
<meta charset="utf-8">
<title>Hullwrap.com – Product</title>
<link href="https://fonts.googleapis.com/css2?family=Arimo:wght@400;700&family=Roboto:wght@400;500;700&display=swap" rel="stylesheet">
<style>
:root{
  --blue:#1d6fc4;
  --blue-dark:#0b3f8f;
  --orange:#e8611a;
  --orange-bright:#ff7a00;
  --sale:#e0502a;
  --star:#f29a00;
  --text:#222;
  --muted:#555;
  --line:#d8d8d8;
  --bar:#3a3a3a;
  --green:#7cb518;
  --page:#f2f2f2;
}
*{box-sizing:border-box;margin:0;padding:0}
html,body{width:727px;height:1200px;overflow:hidden}
body{position:relative;background:var(--page);font-family:"Arimo",sans-serif;color:var(--text);font-size:7px}
.abs{position:absolute}
.header{left:0;top:0;width:727px;height:46px;background:#fff}
.brand{left:94px;top:10px;font:700 24px "Arimo",sans-serif;color:var(--blue);letter-spacing:-.3px}
.phone{right:92px;top:9px;text-align:right;color:var(--blue);font:700 15px "Arimo",sans-serif}
.phone small{display:block;font:400 6.5px "Arimo",sans-serif;color:#666;margin-top:1px}
.phone svg{vertical-align:-2px;margin-right:4px}
.nav{left:0;top:46px;width:727px;height:22px;background:linear-gradient(#fafafa,#e6e6e6);border-top:1px solid #ddd;border-bottom:1px solid #ccc}
.nav a{position:absolute;top:6px;font:400 8.5px "Arimo",sans-serif;color:#333;text-decoration:none}
.checkout{left:526px;top:45px;width:109px;height:18px;background:var(--blue);color:#fff;font:700 6.5px "Arimo",sans-serif;display:flex;align-items:center;gap:5px;padding-left:8px;border-radius:2px}
.crumbs{left:0;top:69px;width:727px;height:21px;background:var(--bar);color:#ddd;font:400 7.5px "Arimo",sans-serif;padding:4px 0 0 105px}
.crumbs b{color:#fff;font-weight:400}
.panel{left:95px;top:90px;width:540px;height:834px;background:#fff;box-shadow:0 1px 3px rgba(0,0,0,.18)}
.hero{left:14px;top:17px;width:323px;height:166px;border:1px solid var(--line);padding:6px}
.hero div{width:100%;height:100%;background:linear-gradient(160deg,#fff 20%,#3a47a0 45%,#dcdcdc 70%,#fff)}
.thumbs{left:14px;top:188px;width:323px;height:60px;border:1px solid var(--line)}
.thumb{position:absolute;top:8px;width:43px;height:43px}
.thumbs .arr{position:absolute;top:22px;color:#aaa;font-size:10px}
.title{left:357px;top:14px;width:150px;font:500 13.5px "Roboto",sans-serif;line-height:16px;color:#333}
.stars{color:var(--star);letter-spacing:.5px}
.rate{left:357px;top:54px;font-size:8px}
.rate span{color:var(--orange)}
.old{left:357px;top:72px;font:700 8px "Arimo",sans-serif;color:#888;text-decoration:line-through}
.onsale{left:357px;top:86px;font:700 8px "Arimo",sans-serif}
.onsale span{color:var(--orange);font-weight:400}
.price{left:357px;top:100px;font:700 14px "Arimo",sans-serif;color:var(--sale)}
.field{left:357px;font-size:7.5px;display:flex;align-items:center;gap:6px}
.select{border:1px solid #aaa;height:12px;padding:0 4px;display:flex;align-items:center;gap:6px;font-size:7px;background:#fff}
.swatch{width:10px;height:10px;display:inline-block}
.rule{left:357px;top:171px;width:165px;height:1px;background:var(--line)}
.opts{left:357px;top:181px;width:165px;list-style:none}
.opts li{display:flex;align-items:center;height:13.3px;font-size:7px}
.opts i{width:8px;height:8px;border:1px solid #888;border-radius:2px;margin-right:7px}
.opts em{margin-left:auto;font-style:normal;color:var(--orange)}
.cart{left:359px;top:240px;width:163px;height:21px;background:linear-gradient(var(--orange-bright),var(--orange));color:#fff;font:400 13px "Roboto",sans-serif;text-align:center;line-height:21px}
.ship{left:359px;top:268px;width:163px;text-align:center;color:#3c8a1f;font-style:italic;font-size:7px}
.also{left:359px;top:311px;width:163px;height:25px;background:var(--bar);color:#fff;font:700 8px "Arimo",sans-serif;text-align:center;line-height:25px;border-radius:2px}
.card{left:359px;width:163px;height:185px;background:#fff;box-shadow:0 1px 3px rgba(0,0,0,.25)}
.card .pic{position:absolute;left:12px;top:12px;width:139px;height:58px}
.card p{position:absolute;top:89px;width:100%;text-align:center;font-size:6.8px;line-height:8px;padding:0 10px}
.card .tag{position:absolute;top:111px;width:100%;height:20px;background:var(--sale);color:#fff;font:700 8px "Arimo",sans-serif;text-align:center;line-height:20px}
.card dl{position:absolute;left:9px;top:136px;font-size:7px;line-height:13px}
.card .free{color:var(--orange)}
.h{font:700 8.5px "Arimo",sans-serif}
.desc{left:14px;top:286px;width:326px}
.desc p{margin-top:6px;font-size:6.8px;line-height:9px;color:#333}
.feat{left:14px;top:363px;width:326px}
.feat ul{list-style:none;margin-top:2px}
.feat li{font-size:6.8px;height:26.2px;padding-left:12px;position:relative;padding-top:5px;color:#333}
.feat li:before{content:"";position:absolute;left:2px;top:8px;width:3px;height:3px;border-radius:50%;background:#333}
.avg{left:14px;top:588px;font:700 8px "Arimo",sans-serif;display:flex;gap:16px;align-items:center}
.avg span{font-weight:400;font-size:7px}
.review{left:14px;width:330px}
.review .t{font:700 8px "Arimo",sans-serif}
.review .by{font-size:7px;margin-top:4px}
.review p{font-size:6.8px;line-height:9.5px;color:#444;margin-top:5px}
.more{left:13px;top:787px;width:80px;height:25px;background:linear-gradient(#fafafa,#e4e4e4);border:1px solid #ccc;box-shadow:0 1px 2px rgba(0,0,0,.15);font-size:8px;text-align:center;line-height:23px}
.news h2{position:absolute;left:95px;top:950px;font:700 14px "Arimo",sans-serif;color:#1a76b5}
.news p{position:absolute;left:95px;top:973px;width:200px;font-size:7px;line-height:8.5px;color:#444}
.email{left:324px;top:949px;width:298px;height:35px;border-radius:18px;background:#e6e6e6;border:1px solid #c8c8c8;box-shadow:inset 0 1px 3px rgba(0,0,0,.15)}
.email span{position:absolute;left:13px;top:11px;font:italic 400 11px "Arimo",sans-serif;color:#999}
.signup{position:absolute;right:3px;top:3px;width:92px;height:27px;border-radius:14px;background:linear-gradient(#8fd12a,#5e9a0f);color:#fff;font:700 11px "Arimo",sans-serif;text-align:center;line-height:27px}
.scene{left:0;top:1010px;width:727px;height:190px;background:linear-gradient(#f4f5f7 0%,#b9c6d3 18%,#5f7a67 40%,#3f6ea6 55%,#1f4fa3 75%,#0f2f86 100%)}
.strip{left:92px;top:1124px;width:544px;height:22px;background:linear-gradient(#1f4fb0,#0c2f8a);border:1px solid #5a7fd0;color:#fff;font:700 6.5px "Arimo",sans-serif}
.strip .win{position:absolute;left:13px;top:7px}
.strip .box{position:absolute;left:146px;top:5px;width:103px;height:11px;background:#fff}
.strip .sub{position:absolute;left:249px;top:5px;width:40px;height:11px;background:var(--orange-bright);font-size:6px;line-height:11px;text-align:center;font-weight:400}
.strip .links{position:absolute;right:13px;top:7px;text-decoration:underline}
.copy{left:0;top:1166px;width:727px;text-align:center;font-size:6px;line-height:8px;color:#8fa3d3}
.copy u{color:#fff}
</style>
</head>
<body>
<header class="abs header"></header>
<div class="abs brand">Hullwrap.com</div>
<div class="abs phone">
  <svg width="13" height="10" viewBox="0 0 13 10"><path d="M1 3c3-3 8-3 11 0l-2 2-2-1V2H5v2L3 5z" fill="#1d6fc4"/><rect x="3" y="5" width="7" height="4" rx="1" fill="#1d6fc4"/></svg>(800) 555-0142
  <small>Store Hours(M-F, 9:30AM - 6PM PST)</small>
</div>
<nav class="abs nav">
  <a style="left:105px">Boat Covers</a>
  <a style="left:182px">Bass Boat Covers</a>
  <a style="left:282px">T Top Boat Covers</a>
  <a style="left:385px">Bimini Tops</a>
  <a style="left:460px">Jet Ski Covers</a>
</nav>
<div class="abs checkout">
  <svg width="10" height="8" viewBox="0 0 10 8"><path d="M0 1h2l1 4h5l1-3H3" stroke="#fff" fill="none"/><circle cx="4" cy="7" r=".9" fill="#fff"/><circle cx="7.5" cy="7" r=".9" fill="#fff"/></svg>
  <span>CHECKOUT : <span style="font-weight:400">(0) Items ▾</span></span>
</div>
<div class="abs crumbs">Home &nbsp;›&nbsp; Boat Covers &nbsp;›&nbsp; Runabout w &nbsp;›&nbsp; <b>up to 18'8" Wide</b></div>

<main class="abs panel">
  <div class="abs hero"><div role="img" aria-label="Blue boat cover on a runabout boat on a trailer"></div></div>
  <div class="abs thumbs">
    <span class="arr" style="left:8px">‹</span>
    <div class="thumb" role="img" aria-label="Product badge" style="left:30px;background:linear-gradient(#eee,#8a2a20)"></div>
    <div class="thumb" role="img" aria-label="Cover fabric" style="left:87px;background:linear-gradient(#2a5aa0,#173c70)"></div>
    <div class="thumb" role="img" aria-label="Strap detail" style="left:144px;background:linear-gradient(#ddd,#444)"></div>
    <div class="thumb" role="img" aria-label="Buckle detail" style="left:201px;background:linear-gradient(#ccc,#333)"></div>
    <div class="thumb" role="img" aria-label="Tie-down detail" style="left:258px;background:linear-gradient(#eee,#111)"></div>
    <span class="arr" style="right:8px">›</span>
  </div>

  <h1 class="abs title">Lorem ipsum dolor sit amet cover</h1>
  <div class="abs rate"><span class="stars">★★★★★</span> <span>(1,471)</span></div>
  <div class="abs old">$248.00</div>
  <div class="abs onsale">On Sale : <span>10% Off</span></div>
  <div class="abs price">$223.20</div>
  <div class="abs field" style="top:128px">Color :
    <span class="select" style="width:84px">Choose an optiuon <span style="margin-left:auto">▾</span></span>
    <span class="swatch" style="background:#1d7cd0"></span><span class="swatch" style="background:#777"></span>
  </div>
  <div class="abs field" style="top:149px">Quantity :
    <span class="select" style="width:27px">1 <span style="margin-left:auto">▾</span></span>
  </div>
  <div class="abs rule"></div>
  <ul class="abs opts">
    <li><i></i>ellentesque ligula dui condim<em>$25.00</em></li>
    <li><i></i>sit amet scelerisque eu, sodales<em>$30.00</em></li>
    <li><i></i>Aenean tincidunt, neque at<em>$11.00</em></li>
    <li><i></i>imperdiet sodales, elit libero<em>$21.00</em></li>
  </ul>
  <div class="abs cart">ADD TO CART</div>
  <div class="abs ship">🚚 Free Shipping!</div>
  <div class="abs also">You may also like</div>

  <article class="abs card" style="top:352px">
    <div class="pic" role="img" aria-label="Grey covered boat on trailer" style="background:linear-gradient(#fff 20%,#4c5660 50%,#fff 85%)"></div>
    <p>Lorem ipsum dolor sit amet, consectetur adipiscing elit.</p>
    <div class="tag">ON SALE</div>
    <dl><dt>From &nbsp;: &nbsp;$152.30</dt><dt class="free">Free Shipping</dt><dt>Rating &nbsp;<span class="stars">★★★★★</span> &nbsp;(1k+)</dt></dl>
  </article>
  <article class="abs card" style="top:548px">
    <div class="pic" role="img" aria-label="Red covered boat with tower on trailer" style="background:linear-gradient(#fff 15%,#d83040 50%,#fff 85%)"></div>
    <p>Lorem ipsum dolor sit amet, consectetur adipiscing elit.</p>
    <div class="tag">ON SALE</div>
    <dl><dt>From &nbsp;: &nbsp;$152.30</dt><dt class="free">Free Shipping</dt><dt>Rating &nbsp;<span class="stars">★★★★★</span> &nbsp;(1k+)</dt></dl>
  </article>

  <section class="abs desc">
    <div class="h">Description :</div>
    <p>Maecenas id dictum risus. Pellentesque aliquam augue eget fringilla feugiat. In hendrerit, est sed faucibus eleifend, ligula quam varius sapien, a efficitur orci velit a tellus. Aenean faucibus aliquet lobortis. Ut sit amet elit ligula. Nunc sit amet luctus erat. Vestibulum urna nulla, laoreet nec tempus at, eleifend eu tellus. Nunc sit amet elit a risus iaculis consectetur non accumsan mauris.</p>
  </section>
  <section class="abs feat">
    <div class="h">Features :</div>
    <ul>
      <li>Maecenas id dictum risus. Pellentesque aliquam</li>
      <li>augue eget fringilla feugiat. In hendrerit, est sed</li>
      <li>faucibus eleifend, ligula quam varius sapien,</li>
      <li>Aenean faucibus aliquet lobortis.</li>
      <li>Ut sit amet elit ligula. Nunc sit amet luctus erat.</li>
      <li>Vestibulum urna nulla, laoreet nec tempus at,</li>
      <li>eleifend eu tellus. Nunc sit amet elit a risus iaculis</li>
      <li>consectetur non accumsan mauris.</li>
    </ul>
  </section>
  <div class="abs avg">Average customer rating : <span><span class="stars" style="font-size:9px">★★★★★</span> (4.8)</span></div>

  <section class="abs review" style="top:607px">
    <div class="t"><span class="stars">★★★★★</span> Great Boat Cover</div>
    <div class="by">Reviewed by Dan Porter (LOREM IPSUM DOLOR, FL, USA) - Feb 22, 2016 5:34 PM.</div>
    <p>Lorem ipsum dolor sit amet, consectetur adipiscing elit. Donec scelerisque sagittis purus. Donec ac metus sem. Cras sapien mauris, tincidunt ut laoreet ut.</p>
  </section>
  <section class="abs review" style="top:666px">
    <div class="t"><span class="stars">★★★★★</span> Great Boat Cover</div>
    <div class="by">Reviewed by Dan Porter (LOREM IPSUM DOLOR, FL, USA) - Feb 22, 2016 5:34 PM.</div>
    <p>Lorem ipsum dolor sit amet, consectetur adipiscing elit. Donec scelerisque sagittis purus. Donec ac metus sem. Cras sapien mauris, tincidunt ut laoreet ut.</p>
  </section>
  <section class="abs review" style="top:726px">
    <div class="t"><span class="stars">★★★★★</span> Great Boat Cover</div>
    <div class="by">Reviewed by Dan Porter (LOREM IPSUM DOLOR, FL, USA) - Feb 22, 2016 5:34 PM.</div>
    <p>Lorem ipsum dolor sit amet, consectetur adipiscing elit. Donec scelerisque sagittis purus. Donec ac metus sem. Cras sapien mauris, tincidunt ut laoreet ut.</p>
  </section>
  <div class="abs more">Load more</div>
</main>

<section class="news">
  <h2>Subscribe to our Newsletter</h2>
  <p>Lorem ipsum dolor sit amet, consectetur adipiscing elit. Pellentesque ligula dui.</p>
</section>
<div class="abs email"><span>Enter Your Email</span><div class="signup">Sign Up</div></div>

<div class="abs scene" role="img" aria-label="Harbor with sailboats below misty mountains"></div>
<div class="abs strip">
  <span class="win">Sign Up To Win A FREE Boat Cover!</span>
  <span class="box"></span><span class="sub">Subscribe ›</span>
  <span class="links">Exchanges &amp; Returns &nbsp; Contact Us</span>
</div>
<footer class="abs copy">Copyright © 2016 Hullwrap.com. All Rights Reserved<br>210 Harbor Lane, Easton NY 10999<br><u>Privacy Policy</u></footer>
</body>
</html>
```